eCommerce Landing Page Design for Wine Accessories using PageFly

Need to develop a landing page template that can be used for ecommerce products. This template needs to be built in PageFly (shopify App) if not in Pagefly, need an integrated app with shopify to maintain the correct url. The website is www.corklanehub.com. The template will be built using one product as an example. Copy and product images will be provided. the Landing page also must have "15% Off" and "free shipping" somewhere on the page

Although part of a website, I am open to different options on design

Target Market(s)

Wine drinkers

Requirements
Must have
• Built in PageFly (shopify App)
• Featured Product
• 15% Off
• Free Shipping
• High Converting with add to cart actions directly on the page

```html
<!DOCTYPE html>
<html lang="en">
<head>
<meta charset="utf-8">
<title>Cork Lane Hub – Wine Accessories</title>
<link rel="stylesheet" href="https://fonts.googleapis.com/css2?family=Open+Sans:wght@400;600;700&family=Playfair+Display:wght@400;700&family=Cinzel:wght@400;700&display=swap">
<style>
:root{
  --red:#b5121b;
  --red-dark:#8e0d14;
  --ink:#222;
  --text:#555;
  --muted:#999;
  --line:#e2e2e2;
  --soft:#f5f5f5;
  --black:#111;
  --white:#fff;
  --sans:'Open Sans',Arial,sans-serif;
  --serif:'Playfair Display',Georgia,serif;
  --caps:'Cinzel',Georgia,serif;
}
*{box-sizing:border-box;margin:0;padding:0}
html,body{width:1200px;height:5000px;overflow:hidden}
body{position:relative;background:var(--white);font-family:var(--sans);color:var(--text);font-size:13px}
.section{position:absolute;left:0;width:1200px}
.wrap{width:1000px;margin:0 auto;position:relative}

/* top bar */
.topbar{top:0;height:40px;border-bottom:1px solid var(--line);font-size:11px;color:#666}
.topbar .wrap{display:flex;align-items:center;height:40px;gap:28px}
.topbar .right{margin-left:auto;display:flex;gap:24px;align-items:center}
.search{width:190px;height:26px;border:1px solid var(--line);display:flex;align-items:center;justify-content:space-between;padding:0 8px;color:#aaa}

/* header */
.header{top:40px;height:125px}
.header .wrap{height:125px;display:flex;align-items:center}
.ship{display:flex;gap:12px;align-items:center;font-size:11px;color:#444;width:330px}
.ship strong{display:block;color:var(--red);font-size:12px}
.brand{flex:1;display:flex;justify-content:center;align-items:center;gap:10px;font-family:var(--sans);font-weight:700;font-size:30px;color:var(--red)}
.brand .dot{width:14px;height:14px;border-radius:50%;background:var(--red)}
.cart{width:330px;display:flex;justify-content:flex-end;position:relative}
.cart .badge{position:absolute;right:-10px;top:-8px;width:20px;height:20px;border-radius:50%;background:var(--red);color:#fff;font-size:10px;display:flex;align-items:center;justify-content:center}

/* nav */
.nav{top:165px;height:42px;background:var(--red)}
.nav ul{list-style:none;display:flex;height:42px;align-items:center}
.nav li{color:#fff;font-size:12px;font-weight:700;padding:0 13px;height:42px;line-height:42px}
.nav li.active{background:var(--red-dark)}

/* hero */
.hero{top:207px;height:410px;background:linear-gradient(90deg,#c9c3bb 0%,#d8cfc2 45%,#e4d9c7 100%)}
.hero .text{position:absolute;left:655px;top:110px}
.hero h1{font-family:var(--serif);font-size:54px;color:var(--ink);font-weight:700}
.hero p{font-size:14px;color:#555;margin:8px 0 20px}
.btn-outline{display:inline-block;border:2px solid var(--red);color:var(--red);font-size:12px;font-weight:700;padding:8px 18px}
.arrow{position:absolute;width:30px;height:30px;border-radius:50%;background:rgba(255,255,255,.8);display:flex;align-items:center;justify-content:center;color:#666;font-size:14px}
.dots{position:absolute;display:flex;gap:6px}
.dots i{width:8px;height:8px;border-radius:50%;background:#ccc;display:block}
.dots i.on{background:var(--red)}

/* tiles */
.tiles{top:650px;height:290px}
.tiles .wrap{display:flex;gap:35px}
.tile{width:310px;height:290px;position:relative}
.tile .label{position:absolute;left:0;right:0;bottom:0;height:44px;background:rgba(255,255,255,.9);display:flex;align-items:center;justify-content:center;font-size:13px;font-weight:700;color:var(--ink)}
.tile .label.mid{bottom:auto;top:123px;background:var(--black);color:#fff}
.ph-silver{background:linear-gradient(160deg,#d9dcdd,#a9aeb1)}
.ph-red{background:linear-gradient(160deg,#f1e3d3,#b0141c 70%)}
.ph-teal{background:linear-gradient(160deg,#e5e9e6,#6cb7a3)}

/* section titles */
.title{height:40px;display:flex;align-items:center;gap:20px}
.title::before,.title::after{content:"";flex:1;border-top:1px dotted #aaa}
.title h2{font-family:var(--serif);font-weight:400;font-size:27px;letter-spacing:2px;color:var(--ink);text-transform:uppercase}
.tabs{display:flex;justify-content:center;gap:6px;margin-top:33px}
.tabs span{border:1px solid var(--line);font-size:11px;padding:8px 18px;color:#444}
.tabs span.on{background:var(--red);border-color:var(--red);color:#fff;font-weight:700}

/* products */
.products{display:flex;gap:20px;margin-top:32px;position:relative}
.card{width:235px;text-align:center}
.card .img{height:225px;position:relative}
.tag{position:absolute;left:10px;top:10px;background:var(--black);color:#fff;font-size:9px;font-weight:700;padding:3px 7px}
.card h3{font-size:15px;font-weight:400;color:var(--ink);margin-top:14px}
.price{color:var(--muted);font-size:14px;margin-top:4px}
.btn{display:inline-block;background:var(--red);color:#fff;font-size:11px;font-weight:700;padding:8px 14px}
.card .btn{margin-top:14px}
.side-arrow{position:absolute;top:95px;width:26px;height:26px;border-radius:50%;border:1px solid #ddd;display:flex;align-items:center;justify-content:center;font-size:12px;color:#888;background:#fff}
.ph-blue{background:linear-gradient(160deg,#f3f1ee,#a9c4d6)}
.ph-wine{background:linear-gradient(160deg,#f3f1ee,#b0141c)}
.ph-steel{background:linear-gradient(160deg,#f3f1ee,#9ea3a6)}
.ph-purple{background:linear-gradient(160deg,#f3f1ee,#7b2f8f)}
.ph-mint{background:linear-gradient(160deg,#f3f1ee,#5fc3a9)}
.ph-rose{background:linear-gradient(160deg,#f3f1ee,#a11a4b)}
.ph-lime{background:linear-gradient(160deg,#f3f1ee,#9ab83a)}
.ph-white{background:linear-gradient(160deg,#f3f1ee,#cfcfcf)}

.featured{top:1027px}
.popular{top:2600px}

/* sale */
.sale{top:1610px;height:473px}
.sale .wrap{height:473px;background:var(--soft);display:flex;align-items:center;padding:0 20px}
.sale .img{width:453px;height:420px;background:linear-gradient(160deg,#cfd2d4,#d86b8c 60%,#8a6a4d)}
.sale .info{flex:1;text-align:center;padding:0 30px}
.sale h2{font-family:var(--serif);font-size:30px;font-weight:400;color:var(--ink);letter-spacing:1px}
.sale h3{color:var(--red);font-size:14px;font-weight:700;margin-top:12px;line-height:1.5}
.sale p{font-size:11px;color:var(--muted);margin-top:10px}
.sale .prices{font-size:24px;margin-top:22px;color:var(--ink)}
.sale .prices s{color:var(--muted);margin-right:8px}
.stars{color:#e6a700;font-size:16px;margin-top:10px;letter-spacing:2px}
.stars .off{color:#ccc}
.buy{display:flex;justify-content:center;align-items:center;gap:50px;margin-top:16px;padding-left:90px}
.seal{width:80px;height:80px;border-radius:50%;background:#c17a1c}
.share{display:flex;justify-content:center;gap:8px;margin-top:14px}
.share span{border:1px solid var(--line);background:#fff;font-size:10px;padding:4px 10px;color:#666}

/* banner */
.banner{top:2173px;height:334px;background:radial-gradient(ellipse at 50% 90%,#7a1016 0%,#3b0c0f 45%,#1c1414 100%);text-align:center;color:#fff}
.banner h2{font-family:var(--caps);font-size:34px;font-weight:700;letter-spacing:2px;margin-top:105px}
.banner p{font-size:14px;color:#ddd;margin:10px 0 22px}

/* testimonial */
.reviews{top:3200px}
.avatar{width:100px;height:100px;border-radius:50%;background:linear-gradient(160deg,#e6ddd4,#8a7566);margin:12px auto 0}
.quote{width:860px;margin:32px auto 0;text-align:center;font-size:12px;line-height:1.9;color:#666;position:relative}
.who{text-align:center;color:var(--red);font-weight:700;font-size:14px;margin-top:18px;letter-spacing:1px}
.reviews .dots{position:static;justify-content:center;margin-top:14px}

/* brands */
.brands{top:3617px}
.logos{display:flex;justify-content:space-around;align-items:center;margin-top:52px;padding:0 40px;position:relative}
.logos span{font-weight:700;font-size:18px;color:var(--ink);letter-spacing:1px}

/* blog */
.blog{top:3807px}
.posts{display:flex;gap:35px;margin-top:26px}
.post{width:310px;height:444px;border:1px solid var(--line)}
.post .img{height:240px;position:relative}
.date{position:absolute;left:12px;top:0;background:var(--red);color:#fff;font-size:13px;font-weight:700;padding:8px 10px;text-align:center;line-height:1.3}
.post .body{padding:18px 16px}
.post h3{font-size:16px;font-weight:600;color:var(--ink)}
.meta{font-size:11px;color:var(--muted);margin-top:8px}
.meta b{color:var(--red);font-weight:400}
.post p{font-size:11px;color:#777;line-height:1.7;margin-top:10px}
.more{color:var(--red);font-size:12px;font-weight:700;margin-top:8px;display:block}
.ph-blog1{background:linear-gradient(160deg,#ddd,#2a2a2a)}
.ph-blog2{background:linear-gradient(160deg,#1a1a1a,#8c0d15)}
.ph-blog3{background:linear-gradient(160deg,#f4e8e1,#c4394a)}
.viewall{top:4377px;text-align:center}
.viewall span{display:inline-block;border:1px solid #ccc;font-size:11px;font-weight:700;padding:10px 22px;color:#333}

/* newsletter */
.newsletter{top:4483px;height:150px;background:var(--red);color:#fff}
.newsletter .wrap{display:flex;align-items:center;height:150px;justify-content:space-between}
.newsletter h2{font-size:18px;font-weight:700}
.newsletter p{font-size:12px;margin-top:6px;color:#f2d6d8}
.form{display:flex}
.form .field{width:460px;height:42px;background:#fff;color:#aaa;font-size:12px;padding:0 14px;display:flex;align-items:center}
.form .go{width:130px;height:42px;background:var(--black);color:#fff;font-size:12px;font-weight:700;display:flex;align-items:center;justify-content:center}

/* footer */
.footer{top:4633px;height:317px;background:var(--black);color:#ccc}
.footer .wrap{display:flex;padding-top:45px}
.f-brand{width:345px;padding-top:50px}
.f-brand .brand{justify-content:flex-start;color:#fff;font-size:30px}
.f-brand .brand .dot{background:#fff}
.social{display:flex;gap:10px;margin-top:28px;padding-left:20px}
.social i{width:36px;height:36px;border-radius:50%;border:1px solid #666;display:block}
.col h4{color:#fff;font-size:14px;font-weight:700;margin-bottom:20px}
.col ul{list-style:none;font-size:12px;line-height:2.5}
.col li::before{content:"›";color:#fff;margin-right:12px}
.contact{width:320px}
.contact .row{display:flex;gap:12px;font-size:12px;line-height:1.7;margin-bottom:16px}
.menus{width:180px}
.bottombar{top:4950px;height:50px;background:var(--black);border-top:1px solid #2a2a2a;font-size:11px;color:#999}
.bottombar .wrap{display:flex;align-items:center;height:50px;justify-content:space-between}
.cards{display:flex;gap:5px}
.cards i{width:34px;height:22px;background:#e9e9e9;border-radius:2px;display:block}
</style>
</head>
<body>

<div class="section topbar">
  <div class="wrap">
    <span>USD ▾</span>
    <span>
      <svg width="10" height="10" viewBox="0 0 24 24"><path d="M6.6 10.8a15 15 0 0 0 6.6 6.6l2.2-2.2c.3-.3.7-.4 1-.2 1.1.4 2.3.6 3.6.6.6 0 1 .4 1 1V20c0 .6-.4 1-1 1C10.6 21 3 13.4 3 4c0-.6.4-1 1-1h3.5c.6 0 1 .4 1 1 0 1.3.2 2.5.6 3.6.1.3 0 .7-.2 1z" fill="#666"/></svg>
      Call Us: 1 800 555 0142</span>
    <div class="right">
      <span>Login</span>
      <span>Register</span>
      <div class="search"><span>Search...</span>
        <svg width="12" height="12" viewBox="0 0 24 24"><circle cx="10" cy="10" r="7" stroke="#333" stroke-width="2.5" fill="none"/><path d="M15 15l6 6" stroke="#333" stroke-width="2.5"/></svg>
      </div>
    </div>
  </div>
</div>

<div class="section header">
  <div class="wrap">
    <div class="ship">
      <svg width="40" height="26" viewBox="0 0 40 26"><rect x="0" y="2" width="24" height="16" fill="#222"/><path d="M24 7h9l5 6v5H24z" fill="#222"/><circle cx="8" cy="21" r="4" fill="#222" stroke="#fff" stroke-width="1.5"/><circle cx="31" cy="21" r="4" fill="#222" stroke="#fff" stroke-width="1.5"/></svg>
      <div><strong>FREE SHIPPING</strong>ON ORDERS OVER $99</div>
    </div>
    <div class="brand"><span class="dot"></span>Cork Lane Hub</div>
    <div class="cart">
      <svg width="34" height="30" viewBox="0 0 34 30"><path d="M1 3h6l4 17h17l4-12H9" stroke="#222" stroke-width="2.6" fill="none"/><circle cx="13" cy="26" r="2.5" fill="#222"/><circle cx="26" cy="26" r="2.5" fill="#222"/></svg>
      <span class="badge">0</span>
    </div>
  </div>
</div>

<nav class="section nav">
  <div class="wrap">
    <ul>
      <li class="active">HOME</li><li>CATALOG</li><li>CHARMS &amp; MARKERS</li><li>COFFEE MUGS</li><li>JEWELRY</li><li>NOVELTY ITEMS</li><li>PHONE CASES</li><li>UNIQUE BOTTLE OPENERS</li><li>MORE...</li>
    </ul>
  </div>
</nav>

<section class="section hero" role="img" aria-label="Photo of stainless steel stemmed wine glasses in red, white, silver and purple on a light backdrop">
  <div class="text">
    <h1>15% OFF</h1>
    <p>Sed picatismnis istate cusantium doloremque</p>
    <span class="btn-outline">SHOP NOW</span>
  </div>
  <span class="arrow" style="left:40px;top:190px">‹</span>
  <span class="arrow" style="right:40px;top:190px">›</span>
  <div class="dots" style="left:655px;top:380px"><i class="on"></i><i></i><i></i><i></i></div>
</section>

<section class="section tiles">
  <div class="wrap">
    <div class="tile ph-silver" role="img" aria-label="Photo of silver stemless wine tumblers"><span class="label">GREEN AVENTURINE</span></div>
    <div class="tile ph-red" role="img" aria-label="Photo of a red insulated wine tumbler"><span class="label mid">SHOP NOW</span></div>
    <div class="tile ph-teal" role="img" aria-label="Photo of teal insulated wine tumblers"><span class="label">ROSE QUARTZ STONE</span></div>
  </div>
</section>

<section class="section featured">
  <div class="wrap">
    <div class="title"><h2>Featured Products</h2></div>
    <div class="tabs"><span class="on">ALL</span><span>LATEST</span><span>NEW ARRIVALS</span></div>
    <div class="products">
      <span class="side-arrow" style="left:-50px">‹</span>
      <div class="card"><div class="img ph-blue" role="img" aria-label="Light blue stemmed wine glass"><span class="tag">NEW</span></div><h3>Quis nostrumexe</h3><div class="price">$86.29</div><span class="btn">ADD TO CART</span></div>
      <div class="card"><div class="img ph-wine" role="img" aria-label="Red stemmed wine glass"><span class="tag">NEW</span></div><h3>Sed quia nonnumq</h3><div class="price">$86.29</div><span class="btn">ADD TO CART</span></div>
      <div class="card"><div class="img ph-steel" role="img" aria-label="Silver stemmed wine glass"><span class="tag">NEW</span></div><h3>Acusantium dolor</h3><div class="price">$86.29</div><span class="btn">ADD TO CART</span></div>
      <div class="card"><div class="img ph-purple" role="img" aria-label="Purple stemmed wine glass"><span class="tag">NEW</span></div><h3>Voluptatem quia</h3><div class="price">$86.29</div><span class="btn">ADD TO CART</span></div>
      <span class="side-arrow" style="right:-50px">›</span>
    </div>
  </div>
</section>

<section class="section sale">
  <div class="wrap">
    <div class="img" role="img" aria-label="Photo of a pink glitter stemmed wine glass on a wooden table"></div>
    <div class="info">
      <h2>ON SALE TODAY</h2>
      <h3>NEW 10OZ STAINLESS DOUBLE WALL<br>INSULATED WINE GLASS</h3>
      <p>Veritatis et quasi architecto beatae vitae dicta sunt explicabo.</p>
      <div class="prices"><s>$34.95</s>$24.95</div>
      <div class="stars">★★★<span class="off">★★</span></div>
      <div class="buy"><span class="btn">ADD TO CART</span><span class="seal" role="img" aria-label="Guarantee badge"></span></div>
      <div class="share"><span>Share</span><span>Post</span><span>Save</span><span>Pin it</span></div>
    </div>
  </div>
</section>

<section class="section banner" role="img" aria-label="Dark photo of red wine in a glass">
  <h2>SEDOEIUS TEMPOR NCIDIDUNT LABORE</h2>
  <p>Nemo enim ipsam voluptatem quia voluptas sit aspernatur odit aut fugit</p>
  <span class="btn">SHOP NOW</span>
</section>

<section class="section popular">
  <div class="wrap">
    <div class="title"><h2>Popular Products</h2></div>
    <div class="tabs"><span class="on">ALL</span><span>TRENDING</span><span>NEW ARRIVALS</span><span>TOP RATED</span></div>
    <div class="products">
      <span class="side-arrow" style="left:-50px">‹</span>
      <div class="card"><div class="img ph-mint" role="img" aria-label="Mint stemmed wine glass"><span class="tag">NEW</span></div><h3>Quis nostrumexe</h3><div class="price">$86.29</div><span class="btn">ADD TO CART</span></div>
      <div class="card"><div class="img ph-rose" role="img" aria-label="Magenta stemmed wine glass"></div><h3>Sed quia nonnumq</h3><div class="price">$86.29</div><span class="btn">ADD TO CART</span></div>
      <div class="card"><div class="img ph-lime" role="img" aria-label="Lime green stemmed wine glass"><span class="tag">NEW</span></div><h3>Acusantium dolor</h3><div class="price">$86.29</div><span class="btn">ADD TO CART</span></div>
      <div class="card"><div class="img ph-white" role="img" aria-label="White stemmed wine glass"></div><h3>Voluptatem quia</h3><div class="price">$86.29</div><span class="btn">ADD TO CART</span></div>
      <span class="side-arrow" style="right:-50px">›</span>
    </div>
  </div>
</section>

<section class="section reviews">
  <div class="wrap">
    <div class="title"><h2>What They Say About Us</h2></div>
    <div class="avatar" role="img" aria-label="Customer portrait"></div>
    <div class="quote">
      “ Lorem ipsum dolor sit amet, consectetur adipiscing elit, sed do eiusmod tempor incididunt ut labore et dolore magna aliqua. Ut enim ad minim veniam, quis nostrud exercitation ullamco laboris nisi ut aliquip ex ea commodo consequat. Duis aute irure dolor in reprehenderit in voluptate velit esse cillum dolore eu fugiat nulla pariatur. ”
      <span class="side-arrow" style="left:-60px;top:22px">‹</span>
      <span class="side-arrow" style="right:-60px;top:22px">›</span>
    </div>
    <div class="who">MARISA QUELL</div>
    <div class="dots"><i class="on"></i><i></i><i></i><i></i></div>
  </div>
</section>

<section class="section brands">
  <div class="wrap">
    <div class="title"><h2>Our Brands</h2></div>
    <div class="logos">
      <span class="side-arrow" style="left:-10px;top:-4px">‹</span>
      <span>HALVORN</span><span>BRINDLE</span><span>OSTRA</span><span>VELLUM</span><span>PENMARK</span><span>BRINDLE</span>
      <span class="side-arrow" style="right:-10px;top:-4px">›</span>
    </div>
  </div>
</section>

<section class="section blog">
  <div class="wrap">
    <div class="title"><h2>Latest From Our Blog</h2></div>
    <div class="posts">
      <article class="post"><div class="img ph-blog1" role="img" aria-label="Photo of friends holding wine glasses"><span class="date">JAN<br>2018</span></div>
        <div class="body"><h3>Lorem ipsum dolor sit amet</h3><div class="meta"><b>Admin</b> &nbsp;|&nbsp; 1 comment</div>
        <p>Duis aute irure dolor in reprehenderit in voluptate velit esse cillum dolore eu fugiat nulla pariatur.</p><span class="more">Read More »</span></div></article>
      <article class="post"><div class="img ph-blog2" role="img" aria-label="Photo of red wine being poured into a glass"><span class="date">JAN<br>2018</span></div>
        <div class="body"><h3>Lorem ipsum dolor sit amet</h3><div class="meta"><b>Admin</b> &nbsp;|&nbsp; 1 comment</div>
        <p>Duis aute irure dolor in reprehenderit in voluptate velit esse cillum dolore eu fugiat nulla pariatur.</p><span class="more">Read More »</span></div></article>
      <article class="post"><div class="img ph-blog3" role="img" aria-label="Photo of a toast with wine glasses and red decorations"><span class="date">JAN<br>2018</span></div>
        <div class="body"><h3>Lorem ipsum dolor sit amet</h3><div class="meta"><b>Admin</b> &nbsp;|&nbsp; 1 comment</div>
        <p>Duis aute irure dolor in reprehenderit in voluptate velit esse cillum dolore eu fugiat nulla pariatur.</p><span class="more">Read More »</span></div></article>
    </div>
  </div>
</section>

<div class="section viewall"><span>VIEW ALL POSTS</span></div>

<section class="section newsletter">
  <div class="wrap">
    <div><h2>NEWSLETTER SIGN UP</h2><p>Get weekly updates about our latest shop and special offers</p></div>
    <div class="form"><span class="field">Email Address</span><span class="go">SUBSCRIBE</span></div>
  </div>
</section>

<footer class="section footer">
  <div class="wrap">
    <div class="f-brand">
      <div class="brand"><span class="dot"></span>Cork Lane Hub</div>
      <div class="social"><i></i><i></i><i></i><i></i></div>
    </div>
    <div class="col contact">
      <h4>CONTACT US</h4>
      <div class="row"><svg width="12" height="16" viewBox="0 0 24 32"><path d="M12 0a11 11 0 0 0-11 11c0 8 11 21 11 21s11-13 11-21A11 11 0 0 0 12 0z" fill="#ccc"/><circle cx="12" cy="11" r="4" fill="#111"/></svg><span>9086, 34 voluptatem actum dolore<br>lauri retnequal ipsa.</span></div>
      <div class="row"><svg width="12" height="12" viewBox="0 0 24 24"><path d="M6.6 10.8a15 15 0 0 0 6.6 6.6l2.2-2.2c.3-.3.7-.4 1-.2 1.1.4 2.3.6 3.6.6.6 0 1 .4 1 1V20c0 .6-.4 1-1 1C10.6 21 3 13.4 3 4c0-.6.4-1 1-1h3.5c.6 0 1 .4 1 1 0 1.3.2 2.5.6 3.6.1.3 0 .7-.2 1z" fill="#ccc"/></svg><span>Phone: 1 800 555 0142</span></div>
      <div class="row"><svg width="13" height="10" viewBox="0 0 26 20"><rect x="1" y="1" width="24" height="18" fill="none" stroke="#ccc" stroke-width="2"/><path d="M1 1l12 10 12-10" fill="none" stroke="#ccc" stroke-width="2"/></svg><span>Email : info@corklanehub.com</span></div>
    </div>
    <div class="col menus"><h4>MENUS</h4><ul><li>Home</li><li>Products</li><li>About us</li><li>Blog</li><li>Careers</li></ul></div>
    <div class="col"><h4>MY ACCOUNT</h4><ul><li>Policies</li><li>Orders</li><li>Return</li><li>Bulk Discount</li><li>Quality</li></ul></div>
  </div>
</footer>

<div class="section bottombar">
  <div class="wrap">
    <span>© copyright 2018 · www.corklanehub.com, All Rights Reserved</span>
    <div class="cards"><i></i><i></i><i></i><i></i><i></i></div>
  </div>
</div>

</body>
</html>
```